RWT Fittings Ltd Business Cards

We need a business card with our business logo. We provide window and door installations on high-rises in west coast British Colombia, Canada.

I would like my business information and details on one side of the card, and the other side the company name with logo

Target Market(s)

General Contractors

Industry/Entity Type

Construction

Contact Information for Business Card

one side i want my company name and logo in the dark theme logo that i provided

Requirements
Must have
• Marco Peltieri, 16045518293, RWTFittings@mailbox-demo.com, 1407-5194 Linden Row Burnaby BC, V5H 2K9, Owner & Manager

```html
<!DOCTYPE html>
<html lang="en">
<head>
<meta charset="utf-8">
<title>RWT Fittings Ltd – Business Cards</title>
<link rel="stylesheet" href="https://fonts.googleapis.com/css2?family=Open+Sans:wght@400;600;700&display=swap">
<style>
  :root {
    --stage: #2b2b2c;
    --card: #1c1c1d;
    --accent: #29a9e1;
    --silver: #9a9a9a;
    --ink-light: #f2f2f2;
  }
  * { margin: 0; padding: 0; box-sizing: border-box; }
  html, body { width: 1200px; height: 780px; overflow: hidden; }
  body {
    background: var(--stage);
    font-family: "Open Sans", Arial, sans-serif;
    display: flex;
    align-items: center;
    justify-content: center;
    gap: 40px;
  }
  .card {
    position: relative;
    width: 540px;
    height: 309px;
    background: var(--card);
    overflow: hidden;
    box-shadow: 0 14px 30px rgba(0,0,0,.45);
  }
  .card__backdrop { position: absolute; inset: 0; }
  .brand {
    position: absolute;
    display: flex;
    align-items: center;
    gap: 10px;
    color: var(--accent);
    font-weight: 700;
    white-space: nowrap;
  }
  .brand__mark { background: var(--accent); flex: none; }
  .card--contact .brand { left: 30px; top: 137px; font-size: 21px; }
  .card--contact .brand__mark { width: 16px; height: 16px; }
  .card--brand .brand { left: 50%; top: 50%; transform: translate(-50%, -50%); font-size: 46px; gap: 16px; }
  .card--brand .brand__mark { width: 34px; height: 34px; }
  .divider {
    position: absolute;
    left: 250px; top: 60px;
    width: 1px; height: 190px;
    background: var(--accent);
  }
  .contact {
    position: absolute;
    left: 268px; top: 68px;
    right: 14px;
    color: var(--ink-light);
    font-size: 13px;
    line-height: 1.6;
    white-space: nowrap;
  }
  .contact__name {
    color: var(--accent);
    font-weight: 700;
    font-size: 21px;
    letter-spacing: .5px;
    line-height: 1.2;
  }
  .contact__role { margin-bottom: 8px; }
  .contact__line { display: flex; align-items: center; gap: 7px; }
  .contact__line svg { width: 11px; height: 11px; flex: none; fill: var(--accent); }
  .contact__address { margin-top: 8px; line-height: 1.45; }
</style>
</head>
<body>

  <section class="card card--contact">
    <svg class="card__backdrop" viewBox="0 0 540 309" preserveAspectRatio="none" aria-hidden="true">
      <path d="M0 0 H150 Q60 10 0 70 Z" fill="var(--silver)"/>
      <path d="M150 0 Q60 10 0 70" fill="none" stroke="var(--accent)" stroke-width="3"/>
      <path d="M0 210 Q170 300 430 309 H0 Z" fill="var(--silver)"/>
      <path d="M0 210 Q170 300 430 309" fill="none" stroke="var(--accent)" stroke-width="3"/>
    </svg>

    <div class="brand"><span class="brand__mark"></span>RWT Fittings Ltd</div>

    <div class="divider"></div>

    <div class="contact">
      <p class="contact__name">MARCO PELTIERI</p>
      <p class="contact__role">Owner &amp; Manager</p>
      <p class="contact__line">
        <svg viewBox="0 0 12 12"><path d="M2.4 0.8 4.2 2.9 3.2 4.2c.7 1.6 2 2.9 3.6 3.6l1.3-1 2.1 1.8-1 1.9C5 10.3 1.7 7 .7 2Z"/></svg>
        16045518293
      </p>
      <p class="contact__line">
        <svg viewBox="0 0 12 12"><path d="M0 2h12v8H0Z M1 3v.4l5 3.2 5-3.2V3Z" fill-rule="evenodd"/></svg>
        RWTFittings@mailbox-demo.com
      </p>
      <p class="contact__line">
        <svg viewBox="0 0 12 12"><circle cx="6" cy="6" r="5.5"/></svg>
        www.rwtfittings-demo.com
      </p>
      <p class="contact__address">1407-5194 Linden Row<br>Burnaby BC, V5H 2K9</p>
    </div>
  </section>

  <section class="card card--brand">
    <div class="brand"><span class="brand__mark"></span>RWT Fittings Ltd</div>
  </section>

</body>
</html>
```